Business Card for premium dental clinic

We are a premium dental clinic based in Brasov, Romania with more than 15 year on the market, providing quality dental treatment made by a team of more specialized dentists, working with modern equipment as a solution to beautiful and healthy teeth.

Our current logo for the clinic use 2 square with colors black and gold - dr Ternisu - studio, using family fonts Bodoni, Myriad Pro and Segoe Print.
Depending on the printing we used some gold CMYK background or gold foil picture background or a gold gradient.
We want a business card:
- eye catching business card
- distinguished business card
- premium design
- to keep the color scheme of black and gold
- to attract the customers to spent time reading the information
- modern concept

```html
<!DOCTYPE html>
<html lang="en">
<head>
<meta charset="utf-8">
<title>Lumen Dental Clinic – Business Card</title>
<link rel="stylesheet" href="https://fonts.googleapis.com/css2?family=Oswald:wght@300;400&family=Roboto:wght@400&display=swap">
<style>
  :root {
    --page: #3a3a3b;
    --card-dark: #2a2a2b;
    --gold-light: #f7d553;
    --gold: #e6b422;
    --gold-deep: #b88a12;
    --white: #ffffff;
    --ink: #141414;
  }
  * { margin: 0; padding: 0; box-sizing: border-box; }
  html, body { width: 799px; height: 1200px; overflow: hidden; }
  body {
    background: var(--page);
    position: relative;
    font-family: "Roboto", Arial, sans-serif;
  }
  .card {
    position: absolute;
    left: 60px;
    width: 680px;
    height: 390px;
    background: var(--card-dark);
    overflow: hidden;
  }
  .card--front { top: 150px; }
  .card--back { top: 660px; }

  .gold-fill {
    background: linear-gradient(135deg, var(--gold-light) 0%, var(--gold) 45%, var(--gold-deep) 75%, var(--gold-light) 100%);
  }

  /* front */
  .front__gold {
    position: absolute; left: 0; top: 0; width: 310px; height: 100%;
  }
  .front__name-box {
    position: absolute; left: 0; top: 100px;
    width: 285px; height: 118px;
    background: var(--white);
    display: flex; align-items: center; justify-content: center;
  }
  .name {
    font-family: "Oswald", "Arial Narrow", sans-serif;
    font-weight: 300;
    color: var(--ink);
    font-size: 62px;
    line-height: 1;
    letter-spacing: -0.5px;
  }
  .name__title { font-size: 40px; }

  .brand {
    position: absolute;
    font-family: "Oswald", "Arial Narrow", sans-serif;
    font-weight: 400;
    text-align: center;
    line-height: 1;
  }
  .brand__word { display: block; font-size: 64px; letter-spacing: 1px; }
  .brand__tag { display: block; font-size: 34px; margin-top: 10px; }
  .front__brand { left: 330px; top: 120px; width: 350px; color: var(--white); }

  /* back */
  .back__art { position: absolute; inset: 0; }
  .back__brand { left: 170px; top: 70px; width: 380px; color: var(--ink); }
  .contact {
    position: absolute; left: 38px; top: 188px;
    list-style: none;
    color: var(--white);
    font-size: 15px;
    line-height: 21px;
  }
  .contact__item { display: flex; align-items: center; gap: 8px; }
  .contact__icon { width: 13px; height: 13px; flex: none; }
  .contact__address { padding-left: 0; }
  .back__name-strip {
    position: absolute; left: 400px; top: 290px;
    width: 280px; height: 74px;
    display: flex; align-items: center; justify-content: center;
  }
  .back__name-strip .name { font-size: 54px; }
  .back__name-strip .name__title { font-size: 34px; }
</style>
</head>
<body>

<section class="card card--front">
  <div class="front__gold gold-fill" role="img" aria-label="Gold foil texture panel"></div>
  <div class="front__name-box">
    <p class="name"><span class="name__title">dr.</span>ternisu</p>
  </div>
  <p class="brand front__brand">
    <span class="brand__word">lumen</span>
    <span class="brand__tag">dental clinic</span>
  </p>
</section>

<section class="card card--back">
  <svg class="back__art" width="680" height="390" viewBox="0 0 680 390" role="img" aria-label="Gold foil texture band with curved edge">
    <defs>
      <linearGradient id="goldGrad" x1="0" y1="0" x2="1" y2="1">
        <stop offset="0" stop-color="var(--gold-light)"/>
        <stop offset="0.45" stop-color="var(--gold)"/>
        <stop offset="0.75" stop-color="var(--gold-deep)"/>
        <stop offset="1" stop-color="var(--gold-light)"/>
      </linearGradient>
    </defs>
    <path d="M0,0 H680 V268 C470,258 210,170 0,72 Z" fill="url(#goldGrad)"/>
    <path d="M0,80 C210,178 470,266 680,276" fill="none" stroke="var(--white)" stroke-width="4"/>
  </svg>

  <p class="brand back__brand">
    <span class="brand__word">lumen</span>
    <span class="brand__tag">dental clinic</span>
  </p>

  <ul class="contact">
    <li class="contact__item">
      <svg class="contact__icon" viewBox="0 0 16 16"><path d="M4 1 L6 5 L4.5 6.5 C5.5 8.5 7.5 10.5 9.5 11.5 L11 10 L15 12 L13.5 15 C7 14.5 1.5 9 1 2.5 Z" fill="var(--gold)"/></svg>
      <span>828-555-0142</span>
    </li>
    <li class="contact__item">
      <svg class="contact__icon" viewBox="0 0 16 16"><rect x="1" y="3" width="14" height="10" fill="var(--gold)"/><path d="M1 3 L8 9 L15 3" fill="none" stroke="var(--card-dark)" stroke-width="1.3"/></svg>
      <span>hello@lumendental.ro</span>
    </li>
    <li class="contact__item">
      <svg class="contact__icon" viewBox="0 0 16 16"><circle cx="8" cy="8" r="7" fill="var(--gold)"/><path d="M1 8 H15 M8 1 C4 5 4 11 8 15 M8 1 C12 5 12 11 8 15" fill="none" stroke="var(--card-dark)" stroke-width="1"/></svg>
      <span>www.lumendental.ro</span>
    </li>
    <li class="contact__address">18 Castle St., Brasov,</li>
    <li class="contact__address">Brasov County, RO 500001</li>
  </ul>

  <div class="back__name-strip gold-fill" role="img" aria-label="Gold foil texture strip behind name">
    <p class="name"><span class="name__title">dr.</span>ternisu</p>
  </div>
</section>

</body>
</html>
```